Construction Company

Design a clutter free business card, it can be double-sided utilizing the logo for VKM Ltd simple with all relevant contact information.

Please also a letterhead design to function for the purposes of invoicing, all mail requirements, with header to be distinctive while the footer ties page together and incorporates all necessary information.

For now, please use generic / dummy text and when a winner is selected, I will disclose the contact information.

Hi Designers! Please read the updated brief which includes the design of a business card and letterhead. Thank you!

```html
<!DOCTYPE html>
<html lang="en">
<head>
<meta charset="utf-8">
<title>VKM Ltd — Letterhead and Business Card</title>
<link href="https://fonts.googleapis.com/css2?family=Lato:wght@300;400;700&family=Open+Sans:wght@400;600;700&family=Pinyon+Script&display=swap" rel="stylesheet">
<style>
  :root {
    --navy: #223a92;
    --gold: #c39a2e;
    --ink: #4e4e4e;
    --paper: #f1f1f1;
    --backdrop: #e6e6e6;
  }
  * { box-sizing: border-box; margin: 0; padding: 0; }
  html, body { width: 1200px; height: 930px; overflow: hidden; background: var(--backdrop); }
  .canvas { position: relative; width: 1200px; height: 930px; background: var(--backdrop); font-family: "Lato", sans-serif; font-variant-ligatures: none; }

  /* Letterhead */
  .letterhead {
    position: absolute; left: 60px; top: 35px; width: 666px; height: 860px;
    background: var(--paper); box-shadow: 0 1px 3px rgba(0,0,0,.12);
  }
  .brand { font-family: "Lato", sans-serif; font-weight: 700; color: var(--navy); white-space: nowrap; display: flex; align-items: center; }
  .brand-dot { display: inline-block; border-radius: 50%; background: var(--navy); }
  .letterhead .brand { position: absolute; left: 50px; top: 46px; font-size: 40px; letter-spacing: .5px; }
  .letterhead .brand-dot { width: 12px; height: 12px; margin-right: 10px; }

  .contact { position: absolute; top: 44px; font-family: "Open Sans", sans-serif; font-size: 11px; line-height: 13.4px; color: #333; }
  .contact-list { left: 343px; list-style: none; }
  .contact-list li { display: flex; align-items: center; gap: 6px; }
  .icon { width: 9px; height: 9px; fill: var(--navy); flex: none; }
  .icon-web { fill: none; stroke: var(--navy); stroke-width: 1; }
  .contact-divider { position: absolute; left: 477px; top: 46px; width: 1px; height: 50px; background: var(--gold); }
  .contact-address { left: 491px; top: 57px; font-style: normal; }

  .letter { position: absolute; left: 75px; top: 175px; width: 514px; color: var(--ink); font-weight: 300; font-size: 10.8px; line-height: 15.4px; }
  .letter-date { margin-bottom: 16px; }
  .recipient { margin-bottom: 30px; }
  .recipient strong { font-weight: 700; color: #222; }
  .salutation { margin-bottom: 15px; }
  .letter p.body { text-align: justify; margin-bottom: 15px; }
  .closing { margin-top: 40px; }
  .signature { font-family: "Pinyon Script", cursive; font-size: 23px; color: #222; margin-top: 4px; margin-left: 4px; font-weight: 400; }

  /* Business cards */
  .card { position: absolute; left: 795px; width: 330px; height: 188px; box-shadow: 0 1px 3px rgba(0,0,0,.12); }
  .card-front { top: 300px; background: var(--paper); }
  .card-back { top: 513px; background: var(--navy); display: flex; align-items: center; justify-content: center; }

  .card-front .brand { position: absolute; left: 30px; top: 78px; font-size: 26px; }
  .card-front .brand-dot { width: 8px; height: 8px; margin-right: 7px; }
  .card-divider { position: absolute; left: 164px; top: 48px; width: 1px; height: 92px; background: var(--gold); }
  .card-details { position: absolute; left: 178px; top: 47px; font-family: "Open Sans", sans-serif; color: #333; }
  .card-name { font-size: 10.5px; font-weight: 700; color: var(--navy); line-height: 12px; }
  .card-role { font-size: 6.5px; color: var(--gold); line-height: 9px; margin-bottom: 9px; }
  .card-address { font-size: 6.8px; line-height: 9.5px; margin-bottom: 6px; }
  .card-contact { list-style: none; font-size: 6.8px; line-height: 9.5px; }
  .card-contact li { display: flex; align-items: center; gap: 4px; }
  .card-contact .icon { width: 6px; height: 6px; }

  .card-back .brand { color: #fff; font-size: 40px; }
  .card-back .brand-dot { background: #fff; width: 12px; height: 12px; margin-right: 10px; }
</style>
</head>
<body>
<svg width="0" height="0" style="position:absolute" aria-hidden="true">
  <symbol id="icon-phone" viewBox="0 0 10 10"><path d="M2.2 0.6l1.6 2-0.9 1.2c0.6 1.2 1.5 2.1 2.7 2.7l1.2-0.9 2 1.6-0.9 1.8C5 8.8 1.2 5 0.4 1.5z"/></symbol>
  <symbol id="icon-fax" viewBox="0 0 10 10"><path d="M2.5 0.5h5v2.3h-5zM0.8 3.3h8.4v4h-1.7v-1.5h-5v1.5H0.8zM3 6.4h4v3.1H3z"/></symbol>
  <symbol id="icon-mail" viewBox="0 0 10 10"><path d="M0.5 2h9v6h-9zM1.2 2.6L5 5.6l3.8-3H1.2z"/></symbol>
  <symbol id="icon-web" viewBox="0 0 10 10"><circle cx="5" cy="5" r="4.2"/><ellipse cx="5" cy="5" rx="1.8" ry="4.2"/><path d="M0.8 5h8.4"/></symbol>
</svg>

<main class="canvas">
  <article class="letterhead">
    <div class="brand"><span class="brand-dot"></span>VKM Ltd</div>

    <ul class="contact contact-list">
      <li><svg class="icon"><use href="#icon-phone"/></svg>210.455.7300</li>
      <li><svg class="icon"><use href="#icon-fax"/></svg>310.622.9400</li>
      <li><svg class="icon"><use href="#icon-mail"/></svg>contact@vkmltd.com</li>
      <li><svg class="icon icon-web"><use href="#icon-web"/></svg>www.vkmltd.com</li>
    </ul>
    <div class="contact-divider"></div>
    <address class="contact contact-address">
      VKM Ltd.<br>Suite 480 Harbour Road<br>Region, Zip 5520, Nation
    </address>

    <section class="letter">
      <p class="letter-date">01 January 2050</p>
      <p class="recipient"><strong>Company (Pvt) Ltd.</strong><br>PO Box 3355 Mainville St<br>Sample City Country 3355</p>
      <p class="salutation">Dear Mark Ellison,</p>
      <p class="body">Lorem ipsum dolor sit amet, consectetuer adipiscing elit, sed diam nonummy nibh euismod tincidunt ut laoreet dolore magna aliquam erat volutpat. Ut wisi enim ad minim veniam, quis nostrud exerci tation ullamcorper suscipit lobortis nisl ut aliquip ex ea commodo consequat. Duis dolore te feugait nulla facilisi. Nam liber tempor cum soluta nobis eleifend option congue nihil imperdiet doming id quod mazim placerat facer possim assum. Lorem ipsum dolor sit amet, consectetuer adipiscing elit, sed diam nonummy nibh euismod tincidunt ut laoreet dolore magna aliquam erat volutpat. Ut wisi enim ad minim veniam, quis nostrud exerci tation ullamcorper suscipit lobortis nisl ut aliquip ex ea commodo consequat.</p>
      <p class="body">Consectetuer adipiscing elit, sed diam nonummy nibh euismod tincidunt ut laoreet dolore magna aliquam erat volutpat. Ut wisi enim ad minim veniam, quis nostrud exerci tation ullamcorper suscipit lobortis nisl ut aliquip ex ea commodo consequat. Consectetuer adipiscing elit, sed diam nonummy nibh euismod tincidunt ut laoreet dolore magna aliquam erat volutpat. Ut wisi enim ad minim veniam, quis nostrud exerci tation ullamcorper suscipit lobortis nisl ut aliquip ex ea commodo consequat.</p>
      <p class="body">Consectetuer adipiscing elit, sed diam nonummy nibh euismod tincidunt ut laoreet dolore magna aliquam erat volutpat. Ut wisi enim ad minim veniam, quis nostrud exerci tation ullamcorper suscipit lobortis nisl ut aliquip ex ea commodo consequat. Consectetuer adipiscing elit, sed diam nonummy nibh euismod tincidunt ut laoreet dolore magna aliquam erat volutpat. Ut wisi enim ad minim veniam, quis nostrud exerci tation ullamcorper suscipit lobortis nisl ut aliquip ex ea commodo consequat.</p>
      <p class="closing">Sincerely Yours</p>
      <p class="signature">Thomas Reed Carver</p>
    </section>
  </article>

  <section class="card card-front">
    <div class="brand"><span class="brand-dot"></span>VKM Ltd</div>
    <div class="card-divider"></div>
    <div class="card-details">
      <p class="card-name">Daniel Hartley</p>
      <p class="card-role">Founder &amp; CEO</p>
      <p class="card-address">Suite 480 Harbour Road<br>Region, Zip 5520, Nation</p>
      <ul class="card-contact">
        <li><svg class="icon"><use href="#icon-phone"/></svg>210.455.7300</li>
        <li><svg class="icon"><use href="#icon-fax"/></svg>310.622.9400</li>
        <li><svg class="icon"><use href="#icon-mail"/></svg>contact@vkmltd.com</li>
        <li><svg class="icon icon-web"><use href="#icon-web"/></svg>www.vkmltd.com</li>
      </ul>
    </div>
  </section>

  <section class="card card-back">
    <div class="brand"><span class="brand-dot"></span>VKM Ltd</div>
  </section>
</main>
</body>
</html>
```